Retro Label for old fashioned soda

We need a label for soda we are having private labeled for our retro, 1950's ice cream shop www.maplefrostparlor.example I don't want the label to look like something from 2017 with a retro feel, but more like an original (possibly kinda cheesy) label you'd see from the 1950's with some of the old catch lines like "tastes great", "invigorating" or "it is refreshing!" The prominent brand should be the name of our ice cream shop, Maple Frost Parlor. the soda is also pure cane sugar so it might be good to have that on somewhere

Label size is 2.4" wide by 4" tall. Here is an example of some retro labels from findwell. I attached on file to this contest but there are more here: https://www.findwell.example/images?q=retro+soda+label&ref=Kx7Qm2Lp9Vt4Rz8Nw3Hd5Jb6Yc1Fg0TsUaWe2Pv7Xo4Ml9Qn8Bk3Dr6Zh5Cy1Ej0Gu7Ai4Ot2Sf9Lw6Nx8Mb3&w=2560&h=1470#img=Pq7Rt2Vw9Xz4Ab:

The label will be the same for all the flavors with the exception of the flavor name changing somewhere on the label. These are the flavors

Root Beer
Orange
Black Cherry
Lemonade
Raspberry Lime -Rickey
White Birch Beer
Lemon Iced Tea
Vanilla Cream
Orange Cream
Sarsaparilla
Ginger Ale

Industry/Entity Type

Shop

Colors

Designer to choose colors to be used in the design.

Requirements
Must have
• retro feel. authentic old fashioned look

```html
<!DOCTYPE html>
<html lang="en">
<head>
<meta charset="utf-8">
<title>Maple Frost Parlor – Vanilla Cream Soda Label</title>
<link rel="stylesheet" href="https://fonts.googleapis.com/css2?family=Josefin+Sans:wght@600&family=Lobster&family=Mr+Dafoe&family=Righteous&display=swap">
<style>
  :root {
    --cream: #fbf5b8;
    --soda-green: #56977a;
    --ink: #1c1c19;
    --checker-dark: #232320;
    --checker-light: #6b6a52;
    --page: #ffffff;
  }
  html, body {
    margin: 0;
    padding: 0;
    width: 1200px;
    height: 1200px;
    overflow: hidden;
    background: var(--page);
  }
  .label {
    position: absolute;
    left: 287px;
    top: 100px;
    width: 625px;
    height: 1000px;
    display: block;
  }
  .tagline {
    font-family: "Mr Dafoe", cursive;
    font-size: 50px;
    fill: var(--ink);
  }
  .brand-name {
    font-family: "Lobster", cursive;
    font-size: 84px;
    fill: var(--ink);
  }
  .flavor-band-text {
    font-family: "Josefin Sans", sans-serif;
    font-weight: 600;
    font-size: 40px;
    letter-spacing: 1px;
    fill: var(--ink);
  }
  .flavor-oval-text {
    font-family: "Righteous", sans-serif;
    font-size: 78px;
    fill: var(--ink);
  }
</style>
</head>
<body>
<svg class="label" viewBox="0 0 600 960" xmlns="http://www.w3.org/2000/svg" aria-label="Maple Frost Parlor vanilla cream soda label">
  <defs>
    <linearGradient id="checker-fill" x1="0" y1="0" x2="1" y2="1">
      <stop offset="0" stop-color="var(--checker-dark)"/>
      <stop offset="0.5" stop-color="var(--checker-light)"/>
      <stop offset="1" stop-color="var(--checker-dark)"/>
    </linearGradient>
    <clipPath id="frame-clip">
      <rect x="27" y="27" width="543" height="906" rx="11"/>
    </clipPath>
  </defs>

  <!-- label ground -->
  <rect class="label-ground" x="0" y="0" width="600" height="960" fill="var(--cream)"/>

  <!-- checkered base -->
  <polygon class="checker-field" role="img" aria-label="Black and cream checkerboard pattern"
           clip-path="url(#frame-clip)"
           points="27,640 570,485 570,935 27,935" fill="url(#checker-fill)"/>

  <!-- green brand panel -->
  <polygon class="brand-panel" points="40,40 560,40 560,483 40,633" fill="var(--soda-green)"/>

  <!-- tagline box -->
  <rect class="tagline-box" x="50" y="49" width="498" height="86" fill="var(--cream)"/>
  <text class="tagline" x="298" y="108" text-anchor="middle">it tastes great !</text>

  <!-- brand name -->
  <text class="brand-name" x="300" y="240" text-anchor="middle">Maple Frost</text>
  <text class="brand-name" x="300" y="345" text-anchor="middle">Parlor</text>

  <!-- flavor band -->
  <polygon class="flavor-band" points="50,518 548,376 555,478 50,622" fill="var(--cream)"/>
  <text class="flavor-band-text" x="300" y="514" text-anchor="middle" transform="rotate(-16 300 500)">VANILLA CREAM</text>

  <!-- outer frame -->
  <rect class="outer-frame" x="27" y="27" width="543" height="906" rx="11" fill="none" stroke="var(--soda-green)" stroke-width="5"/>

  <!-- flavor oval -->
  <ellipse class="flavor-oval" cx="298" cy="776" rx="250" ry="132" fill="var(--cream)" stroke="var(--ink)" stroke-width="2"/>
  <text class="flavor-oval-text" x="298" y="765" text-anchor="middle">vanilla</text>
  <text class="flavor-oval-text" x="298" y="836" text-anchor="middle">cream</text>
</svg>
</body>
</html>
```